Brightvale cleaning and maintenance company

An expansive website whereby we can advertise our commercial cleaning and maintenance services across a service portfolio of commercial cleaning and property maintenance. Whereby potential skilled resources can deposit there resume so we can collaborate and match candidates to a broad range of cleaning and maintenance jobs/projects.
Updates

Looking for more extensive ideas so the front page can change pictures on it with the focus for Brightvale Commercial Cleaning and Maintenance. Also need to bring in all the portfolios we offer including 1. Equipment Cleaning and Sanitisation Services 2. High pressure gurney and play ground equipment cleaning 3. General Cleaning and Property Facilities Management 4. Project and Recruiting Services, to allow for potential professional cleaners, handy man, mechanics, warehousing resources , electricians to deposit there resume. Most of the designers have stuck with the old portfolio categories , however the portfolio of services we offer has been updated so that needs to be reflected in the website. Also not necessary to use all my original photos I would like the opening page of the website to perhaps be able to change and have different pictures is that possible thank you

```html
<!DOCTYPE html>
<html lang="en">
<head>
<meta charset="utf-8">
<title>Brightvale – Commercial Cleaning &amp; Maintenance</title>
<link href="https://fonts.googleapis.com/css2?family=Merriweather:ital,wght@0,300;0,400;0,700;1,400&display=swap" rel="stylesheet">
<style>
:root{
  --navy:#1c3b72;
  --navy-deep:#16305e;
  --orange:#f2410f;
  --grey-band:#f1f1f1;
  --text:#4a4a4a;
  --white:#ffffff;
  --review-bg:#214a87;
}
*{box-sizing:border-box;margin:0;padding:0}
html,body{width:1200px;height:3747px;overflow:hidden}
body{position:relative;font-family:"Merriweather",Georgia,serif;color:var(--text);background:var(--white)}
.abs{position:absolute}

/* header */
.top-rule{left:0;top:0;width:1200px;height:5px;background:var(--orange)}
.brand{display:flex;align-items:center;gap:12px;font-family:"Merriweather",Georgia,serif;font-weight:400;color:var(--orange);font-size:40px;letter-spacing:-0.5px}
.brand-dot{width:42px;height:42px;border-radius:50%;background:var(--navy);flex:none}
.header-brand{left:77px;top:52px}
.head-office{left:737px;top:25px;display:flex;align-items:center;gap:14px;color:var(--navy);font-size:24px;font-weight:700}
.phone-box{width:34px;height:34px;border-radius:6px;background:var(--orange);display:flex;align-items:center;justify-content:center}
.main-nav{left:470px;top:100px;display:flex;gap:36px;font-size:16px;color:#444;letter-spacing:0.3px}
.main-nav .active{color:var(--orange)}

/* hero */
.hero{left:0;top:148px;width:1200px;height:612px;background:linear-gradient(160deg,#6f7780 0%,#3b3f46 35%,#24262b 60%,#5a4a3c 85%,#2b2b2e 100%)}
.hero-wave{left:0;top:660px;width:1200px;height:110px}
.slide-dots{left:1074px;top:430px;width:36px;height:160px;border-radius:18px;background:var(--white);display:flex;flex-direction:column;align-items:center;justify-content:space-around;padding:10px 0}
.slide-dots span{width:14px;height:14px;border-radius:50%;background:var(--navy)}
.slide-dots span.on{background:var(--orange);box-shadow:0 0 0 6px var(--orange)}

/* welcome */
.section-title{width:1200px;left:0;text-align:center;font-size:44px;font-weight:700;color:var(--navy)}
.section-title .hl{color:var(--orange)}
.welcome-title{top:820px}
.welcome-copy{left:180px;top:912px;width:840px;text-align:center;font-size:14.5px;line-height:22.5px;font-weight:300;color:#3d3d3d}
.read-more{left:516px;top:1066px;width:170px;height:44px;border-radius:22px;background:var(--orange);color:var(--white);font-size:16px;font-weight:700;display:flex;align-items:center;padding-left:25px;box-shadow:0 4px 8px rgba(0,0,0,.2)}
.read-more::after{content:"";position:absolute;right:-4px;top:2px;width:40px;height:40px;border-radius:50%;background:var(--navy)}

/* services */
.services{left:0;top:1204px;width:1200px;height:500px;background:var(--grey-band)}
.services-title{top:1255px}
.service-card{top:1361px;width:243px;height:200px}
.service-photo{position:absolute;left:0;top:0;width:243px;height:198px;border-radius:8px}
.service-label{position:absolute;left:40px;top:150px;width:216px;height:82px;background:var(--white);border-radius:6px;transform:skewX(-14deg);box-shadow:0 6px 10px rgba(0,0,0,.12)}
.service-label.featured{background:var(--orange)}
.service-text{position:absolute;right:-4px;top:158px;width:220px;text-align:right;padding-right:22px;color:var(--navy)}
.service-text small{display:block;font-size:12.5px;line-height:14px;font-weight:700}
.service-text strong{display:block;font-size:23px;font-weight:400;margin-top:2px}
.featured-text{color:var(--white)}

/* portfolio */
.portfolio-title{top:1777px}
.tile{border-radius:6px;overflow:hidden}
.tile-cap{position:absolute;left:0;bottom:0;width:100%;background:rgba(28,59,114,.82);color:var(--white);font-size:30px;line-height:36px;padding:14px 32px}
.tile-cap.center{text-align:center}

/* reviews */
.reviews{left:0;top:2650px;width:1200px;height:612px;background:var(--review-bg)}
.reviews-title{top:2712px;color:var(--orange)}
.quote-mark{left:0;width:1200px;top:2790px;text-align:center;font-size:130px;line-height:130px;color:#c9452f;font-weight:700}
.review-text{left:150px;top:2914px;width:900px;text-align:center;color:var(--white);font-style:italic;font-size:31px;line-height:36px}
.stars{left:529px;top:3076px;display:flex;gap:10px}
.stars span{width:28px;height:28px;border-radius:7px;background:var(--orange);display:flex;align-items:center;justify-content:center}
.reviewer{left:0;width:1200px;top:3124px;text-align:center;color:var(--white);font-size:19px;font-weight:700}
.reviewer-role{left:0;width:1200px;top:3150px;text-align:center;color:#dfe6f2;font-size:14px;font-style:italic}

/* footer */
.footer-brand{left:444px;top:3318px}
.footer-nav{left:273px;top:3404px;display:flex;gap:35px;font-size:16px;color:#444}
.footer-nav .active{color:var(--orange)}
.footer-contact{left:250px;top:3460px;display:flex;align-items:center;gap:14px;font-size:14.5px;color:#333}
.footer-contact .sep{color:#777;margin:0 8px}
.footer-contact svg{margin-right:6px}
.social-band{left:0;top:3532px;width:1200px;height:215px;background:var(--orange)}
.social{left:330px;top:3583px;display:flex;gap:34px;color:var(--white);font-size:19px;text-align:center}
.social div{display:flex;flex-direction:column;align-items:center;gap:18px;width:120px}
.social i{width:24px;height:24px;border-radius:50%;background:var(--white);display:block}
.copyright{left:0;width:1200px;top:3684px;text-align:center;color:var(--white);font-size:14.5px}
</style>
</head>
<body>

<div class="abs top-rule"></div>

<header>
  <div class="abs brand header-brand"><span class="brand-dot"></span>Brightvale</div>
  <div class="abs head-office">
    <span class="phone-box"><svg width="18" height="18" viewBox="0 0 24 24"><path fill="#fff" d="M6.6 10.8a15.1 15.1 0 0 0 6.6 6.6l2.2-2.2c.3-.3.7-.4 1-.2 1.1.4 2.3.6 3.6.6.6 0 1 .4 1 1V20c0 .6-.4 1-1 1A17 17 0 0 1 3 4c0-.6.4-1 1-1h3.5c.6 0 1 .4 1 1 0 1.3.2 2.5.6 3.6.1.3 0 .7-.2 1z"/></svg></span>
    HEAD OFFICE: (07) 5550 2184
  </div>
  <nav class="abs main-nav">
    <span class="active">HOME</span><span>ABOUT</span><span>SERVICES</span><span>PORTFOLIO</span><span>REVIEWS</span><span>CONTACT US</span>
  </nav>
</header>

<section>
  <div class="abs hero" role="img" aria-label="Commercial stainless steel kitchen with pendant lamps, rotating hero photograph"></div>
  <div class="abs slide-dots"><span class="on"></span><span></span><span></span><span></span></div>
  <svg class="abs hero-wave" viewBox="0 0 1200 110" preserveAspectRatio="none">
    <path d="M0 45 C250 5 480 20 620 50 C800 90 1000 95 1200 55 L1200 110 L0 110 Z" fill="#16305e"/>
    <path d="M0 45 C250 5 480 20 600 62 C780 108 1000 110 1200 78 L1200 110 L0 110 Z" fill="#ffffff"/>
    <circle cx="600" cy="72" r="34" fill="#ffffff"/>
    <circle cx="600" cy="72" r="26" fill="#1c3b72"/>
  </svg>

  <h1 class="abs section-title welcome-title">Welcome To <span class="hl">Brightvale</span></h1>
  <p class="abs welcome-copy">We are Brightvale, a leading, Australian owned, cleaning services company. When you work with Brightvale it is easy to do business with us. Our people are professional, reliable and service oriented. In every interaction you have; on site, receiving help from our service support staff, or rolling-out new cleaning sites, you will see and feel the benefits of using Brightvale. The pride we take in our work and a prevailing focus on employees, customers and partners, delivers a consistent and superior ongoing service.</p>
  <div class="abs read-more">Read More</div>
</section>

<section>
  <div class="abs services"></div>
  <h2 class="abs section-title services-title"><span class="hl">Our</span> Services</h2>

  <div class="abs service-card" style="left:77px">
    <div class="service-photo" role="img" aria-label="Chef sanitising kitchen equipment" style="background:linear-gradient(135deg,#8b8f95,#d9dde0 55%,#5c6168)"></div>
    <div class="service-label featured"></div>
    <div class="service-text featured-text"><small>Equipment Cleaning &amp;<br>Sanitisation</small><strong>Services</strong></div>
  </div>
  <div class="abs service-card" style="left:345px">
    <div class="service-photo" role="img" aria-label="Worker pressure washing a brick wall" style="background:linear-gradient(135deg,#6c7e8e,#3f4b57 50%,#1f2d3f)"></div>
    <div class="service-label"></div>
    <div class="service-text"><small>High pressure gurney &amp;<br>play ground equipment</small><strong>Cleaning</strong></div>
  </div>
  <div class="abs service-card" style="left:614px">
    <div class="service-photo" role="img" aria-label="Cleaner holding a bucket of cleaning supplies" style="background:linear-gradient(135deg,#e7e3df,#c9c3bc 50%,#9aa7b8)"></div>
    <div class="service-label"></div>
    <div class="service-text"><small>General Cleaning &amp;<br>Property Facilities</small><strong>Management</strong></div>
  </div>
  <div class="abs service-card" style="left:883px">
    <div class="service-photo" role="img" aria-label="Team meeting around a conference table" style="background:linear-gradient(135deg,#d8d9d6,#8b8a86 50%,#3b3a3a)"></div>
    <div class="service-label"></div>
    <div class="service-text" style="top:172px"><small>Project &amp; Recruiting</small><strong>Services</strong></div>
  </div>
</section>

<section>
  <h2 class="abs section-title portfolio-title"><span class="hl">Our</span> Portfolio</h2>

  <div class="abs tile" style="left:74px;top:1881px;width:339px;height:429px;background:linear-gradient(160deg,#e8ecef,#b9c4cf 50%,#6f8aa8)" role="img" aria-label="Window cleaner at work">
    <div class="tile-cap" style="height:150px;padding-top:22px">Potential<br>professional<br>cleaners</div>
  </div>
  <div class="abs tile" style="left:73px;top:2329px;width:339px;height:173px;background:linear-gradient(135deg,#c9d2d8,#7d8b97 50%,#4a5866)" role="img" aria-label="Warehouse shelving aisles">
    <div class="tile-cap center" style="height:100px;padding-top:14px">Warehousing<br>resources</div>
  </div>
  <div class="abs tile" style="left:431px;top:1881px;width:339px;height:301px;background:linear-gradient(135deg,#f0774c,#e9542a 60%,#d9461f)" role="img" aria-label="Handyman carrying a coil of cable">
    <div class="tile-cap center" style="background:none;bottom:38px">Handy man</div>
  </div>
  <div class="abs tile" style="left:431px;top:2202px;width:339px;height:301px;background:linear-gradient(135deg,#8a9197,#c0b48a 50%,#4a5560)" role="img" aria-label="Electrician working at a switchboard">
    <div class="tile-cap center" style="height:140px;padding-top:18px">Electricians to<br>deposit there<br>resume</div>
  </div>
  <div class="abs tile" style="left:785px;top:1881px;width:339px;height:460px;background:linear-gradient(160deg,#4b5158,#2c3e66 55%,#213a70)" role="img" aria-label="Mechanic in blue overalls holding a wrench">
    <div class="tile-cap center" style="height:100px;padding-top:28px">Mechanics</div>
  </div>
</section>

<section>
  <div class="abs reviews"></div>
  <h2 class="abs section-title reviews-title">Reviews</h2>
  <div class="abs quote-mark">“</div>
  <svg class="abs" style="left:104px;top:2920px" width="30" height="60" viewBox="0 0 30 60"><path d="M26 2 L4 30 L26 58" fill="none" stroke="#c8d3e6" stroke-width="2"/></svg>
  <svg class="abs" style="left:1066px;top:2920px" width="30" height="60" viewBox="0 0 30 60"><path d="M4 2 L26 30 L4 58" fill="none" stroke="#c8d3e6" stroke-width="2"/></svg>
  <p class="abs review-text">Sed ut perspiciatis unde omnis iste natus error sit voluptatem accusantium doloremque laudantium, totam rem aperiam, eaque ipsa quae ab illo.</p>
  <div class="abs stars">
    <span><svg width="16" height="16" viewBox="0 0 24 24"><path fill="#fff" d="M12 2l3 7 7 .6-5.3 4.6 1.6 7.1L12 17.6 5.7 21.3l1.6-7.1L2 9.6 9 9z"/></svg></span>
    <span><svg width="16" height="16" viewBox="0 0 24 24"><path fill="#fff" d="M12 2l3 7 7 .6-5.3 4.6 1.6 7.1L12 17.6 5.7 21.3l1.6-7.1L2 9.6 9 9z"/></svg></span>
    <span><svg width="16" height="16" viewBox="0 0 24 24"><path fill="#fff" d="M12 2l3 7 7 .6-5.3 4.6 1.6 7.1L12 17.6 5.7 21.3l1.6-7.1L2 9.6 9 9z"/></svg></span>
    <span><svg width="16" height="16" viewBox="0 0 24 24"><path fill="#fff" d="M12 2l3 7 7 .6-5.3 4.6 1.6 7.1L12 17.6 5.7 21.3l1.6-7.1L2 9.6 9 9z"/></svg></span>
  </div>
  <div class="abs reviewer">Dana R.</div>
  <div class="abs reviewer-role">Cap.ipsum dolor</div>
</section>

<footer>
  <div class="abs brand footer-brand"><span class="brand-dot"></span>Brightvale</div>
  <nav class="abs footer-nav">
    <span class="active">HOME</span><span>ABOUT</span><span>SERVICES</span><span>PORTFOLIO</span><span>REVIEWS</span><span>CONTACT US</span>
  </nav>
  <div class="abs footer-contact">
    <span><svg width="14" height="14" viewBox="0 0 24 24"><path fill="#222" d="M6.6 10.8a15.1 15.1 0 0 0 6.6 6.6l2.2-2.2c.3-.3.7-.4 1-.2 1.1.4 2.3.6 3.6.6.6 0 1 .4 1 1V20c0 .6-.4 1-1 1A17 17 0 0 1 3 4c0-.6.4-1 1-1h3.5c.6 0 1 .4 1 1 0 1.3.2 2.5.6 3.6.1.3 0 .7-.2 1z"/></svg>Landline: 1300 555 270</span>
    <span class="sep">|</span>
    <span><svg width="10" height="14" viewBox="0 0 10 16"><rect x="1" y="1" width="8" height="14" rx="1.5" fill="none" stroke="#222" stroke-width="1.6"/></svg>Mobile: 0400 555 931</span>
    <span class="sep">|</span>
    <span><svg width="14" height="12" viewBox="0 0 16 12"><rect width="16" height="12" rx="1" fill="#222"/><path d="M1 1l7 5 7-5" fill="none" stroke="#fff" stroke-width="1.3"/></svg>service@brightvale.example</span>
  </div>

  <div class="abs social-band"></div>
  <div class="abs social">
    <div><i></i>SOCIALHUB</div>
    <div><i></i>SNAPSHARE</div>
    <div><i></i>CHIRPER</div>
    <div><i></i>PROLINK</div>
  </div>
  <div class="abs copyright">© 2020 &nbsp;|&nbsp; www.brightvale.example</div>
</footer>

</body>
</html>
```